KOVA! Card

The single side "business card" will be utilized to write down product information for our customers. The card needs to include our logo in josefin font and read KOVA! on the front. Our brand colors are espresso brown and copper. The back needs to be white (blank) to allow us to write information down. We want modern, bold, clean and fun.
I have attached a copy of our logo but you do not have to utilize exactly as shown.

```html
<!DOCTYPE html>
<html lang="en">
<head>
<meta charset="utf-8">
<title>KOVA! Card</title>
<link rel="stylesheet" href="https://fonts.googleapis.com/css2?family=Josefin+Sans:wght@400&display=swap">
<style>
  :root {
    --espresso: #2a1912;
    --copper: #c8692a;
    --paper: #ffffff;
    --ink: #2b2320;
    --rule: #9a9a9a;
    --backdrop: #676170;
  }
  * { margin: 0; padding: 0; box-sizing: border-box; }
  html, body {
    width: 1200px;
    height: 900px;
    overflow: hidden;
    background: var(--backdrop);
  }
  .stage {
    width: 1200px;
    height: 900px;
    display: flex;
    align-items: center;
    justify-content: center;
    gap: 60px;
  }
  .card {
    width: 520px;
    height: 296px;
    position: relative;
    box-shadow: 3px 4px 8px rgba(0, 0, 0, 0.45);
  }
  .card-front {
    background: var(--espresso);
    display: flex;
    align-items: center;
    justify-content: center;
  }
  .front-word {
    font-family: "Josefin Sans", sans-serif;
    font-weight: 400;
    font-size: 72px;
    line-height: 1;
    letter-spacing: 0;
    color: var(--copper);
    padding-top: 10px;
  }
  .card-back {
    background: var(--paper);
  }
  .brand {
    position: absolute;
    left: 0;
    right: 0;
    top: 34px;
    text-align center;
    text-align: center;
    font-family: "Josefin Sans", sans-serif;
    font-weight: 400;
    color: var(--ink);
  }
  .brand-name {
    font-size: 30px;
    line-height: 1;
  }
  .brand-tagline {
    font-size: 13px;
    line-height: 1;
    margin-top: 8px;
  }
  .write-lines {
    position: absolute;
    left: 34px;
    top: 0;
  }
</style>
</head>
<body>
  <main class="stage">
    <section class="card card-front">
      <p class="front-word">KOVA!</p>
    </section>
    <section class="card card-back">
      <div class="brand">
        <p class="brand-name">Marlowe</p>
        <p class="brand-tagline">Handmade Goods &amp; Gifts</p>
      </div>
      <svg class="write-lines" width="456" height="296" viewBox="0 0 456 296" aria-hidden="true">
        <g stroke="var(--rule)" stroke-width="1">
          <line x1="0" y1="136.5" x2="456" y2="136.5"/>
          <line x1="0" y1="172.5" x2="456" y2="172.5"/>
          <line x1="0" y1="209.5" x2="456" y2="209.5"/>
          <line x1="0" y1="245.5" x2="456" y2="245.5"/>
        </g>
      </svg>
    </section>
  </main>
</body>
</html>
```